Emerging automotive detailing business

I am starting a small automotive detailing business in hopes of becoming a well-known detailer to work on high end cars. I would like a card to reflect the high quality and time I put into my work. The name of the company is Bright Crest Detailing. I feel like it represents racecars getting off the line at the drag strip as well as an innuendo of "Up the Ladder". I do minor paint correction such as clay barring, multi-step buffing and polishing, waxing, hand washes, etc. I am always striving to learn more and improve my work. My goal is to have total customer satisfaction. This is a female run business but I do not want it to be very girly. Elegant is okay! I have pictures of my personal wrenfield attached, they do not need to be incorporated but if you can think of a cool way to use 1 or all of them, go for it!

Target Market(s)

Anyone that owns a vehicle. Preferably high end vehicles such as Valtori, Castellverde and Morvani but I will also happily work on any car, truck or suv no matter what brand.

Industry/Entity Type

Automotive

Contact Information for Business Card

Bright Crest Detailing
Mira Tolland
4175 Quenhollow Rd
Ashmere PA 17492
Cell phone- call/text- 717-555-0148
email- brightcrestdetails@maildrop-example.com
Instagram: @brightcrestdetailing
Facebook: facebook.com/brightcrestdetailing

Requirements
Must have
• Business name, my name, address, phone number. Listing that I do minor paint correction such as clay barring, multi-step buffing and polishing, waxing, hand washes, interior cleaning, and more. (This last part was in nice to haves but I have realized that I do really want it, so I moved it to must haves.) I want something that is different and eye-catching to my customers. Some people have done this very well with cards already submitted to me, but a lot have not. I didn't mess with the "look and feel bars" much because because I am pretty open to the overall design as long as it is not your basic run of the mill design.
Nice to have
• Something car related. Maybe an appointment time/date line. I do not have a logo, but if you would like to design one and incorporate it, that would be amazing!
Should not have
• Purple and Pink colors. Boring, basic, normal card.

```html
<!DOCTYPE html>
<html lang="en">
<head>
<meta charset="utf-8">
<title>Bright Crest Detailing – Business Card</title>
<link rel="stylesheet" href="https://fonts.googleapis.com/css2?family=Lato:wght@300;400&family=Tinos&display=swap">
<style>
  :root {
    --backdrop: #e9e6e2;
    --card-light: #ffffff;
    --card-dark: #231f1e;
    --ink: #1d1d1d;
    --accent: #f2a320;
    --rule-grey: #5b5654;
    --road-grey: #8d8a88;
    --muted: #b9b4b1;
    --shadow: rgba(0, 0, 0, 0.18);
  }
  html, body {
    margin: 0;
    padding: 0;
    width: 1200px;
    height: 676px;
    overflow: hidden;
    background: var(--backdrop);
  }
  .canvas {
    position: relative;
    width: 1200px;
    height: 676px;
    display: flex;
    align-items: center;
    justify-content: center;
    gap: 60px;
  }
  .card {
    position: relative;
    width: 520px;
    height: 297px;
    box-shadow: 0 10px 28px var(--shadow);
    overflow: hidden;
  }
  p { margin: 0; }

  /* Contact side */
  .card--contact {
    background: var(--card-light);
    color: var(--ink);
    font-family: "Tinos", "Times New Roman", serif;
  }
  .contact__address {
    position: absolute;
    top: 62px;
    right: 70px;
    text-align: right;
    font-size: 19px;
    line-height: 1.15;
  }
  .contact__rule {
    position: absolute;
    left: 0;
    right: 0;
    top: 132px;
    height: 1.5px;
    background: var(--accent);
  }
  .contact__details {
    position: absolute;
    top: 146px;
    left: 44px;
    right: 20px;
    font-size: 18px;
    line-height: 1.2;
  }

  /* Name side */
  .card--identity {
    background: var(--card-dark);
    font-family: "Lato", "Helvetica Neue", Arial, sans-serif;
  }
  .identity__name {
    position: absolute;
    top: 26px;
    left: 128px;
    margin: 0;
    font-weight: 300;
    font-size: 20px;
    color: var(--accent);
    letter-spacing: 0.3px;
  }
  .identity__rule {
    position: absolute;
    top: 60px;
    left: 40px;
    width: 330px;
    height: 1px;
    background: var(--rule-grey);
  }
  .identity__artwork {
    position: absolute;
    top: 74px;
    left: 40px;
    width: 300px;
    height: 100px;
    border-radius: 4px;
    background: linear-gradient(100deg, var(--road-grey) 0%, #5d5957 50%, var(--accent) 100%);
    opacity: 0.85;
  }
  .identity__business {
    position: absolute;
    top: 190px;
    left: 40px;
    margin: 0;
    font-weight: 400;
    font-size: 22px;
    letter-spacing: 1px;
    color: var(--accent);
  }
  .identity__services {
    position: absolute;
    top: 226px;
    left: 40px;
    right: 30px;
    font-weight: 300;
    font-size: 12.5px;
    line-height: 1.45;
    color: var(--muted);
  }
</style>
</head>
<body>
  <main class="canvas">
    <section class="card card--contact" aria-label="Business card, contact side">
      <div class="contact__address">
        <p>4175 Quenhollow Rd</p>
        <p>Ashmere PA 17492</p>
      </div>
      <div class="contact__rule"></div>
      <div class="contact__details">
        <p>Cell phone- call/text- 717-555-0148</p>
        <p>email- brightcrestdetails@maildrop-example.com</p>
        <p>Instagram: @brightcrestdetailing</p>
      </div>
    </section>

    <section class="card card--identity" aria-label="Business card, name side">
      <h1 class="identity__name">Mira Tolland</h1>
      <div class="identity__rule"></div>
      <div class="identity__artwork" role="img" aria-label="Illustration of a winding grey road with dashed centre line leading to the front of an orange sports car"></div>
      <h2 class="identity__business">Bright Crest Detailing</h2>
      <div class="identity__services">
        <p>Minor paint correction · Clay barring · Multi-step buffing &amp; polishing</p>
        <p>Waxing · Hand washes · Interior cleaning &amp; more</p>
      </div>
    </section>
  </main>
</body>
</html>
```